I would like a business card to match my truck wrap and logo. I would like the font to match my existing business card please.

Industry/Entity Type

Painter

Contact Information for Business Card

Rodrigo Fenwar 801-437-2190 Fenwarcoatings.utah@brelmox.com
SERVICES - Custom Paint & Stain, Interior & Exterior, Epoxy Coatings / Garage Floors, Cabinet Refinishing, Log Staining and Refinishing.

Requirements
Nice to have
• I would like to have the white and grey line like the bottom of my vehicle wrap, Light Grey to match my truck also.

```html
<!DOCTYPE html>
<html lang="en">
<head>
<meta charset="UTF-8">
<title>Fenwar Painting – Business Card</title>
<link rel="stylesheet" href="https://fonts.googleapis.com/css2?family=Montserrat:wght@500;700&family=Roboto:wght@400;500&display=swap">
<style>
  :root {
    --backdrop: #2b2b2c;
    --card-dark: #4a4b4d;
    --card-dark-edge: #3c3d3f;
    --brand-blue: #1aa3e3;
    --brand-blue-deep: #0b6fb2;
    --text-light: #ffffff;
    --panel-white: #ffffff;
  }
  * { box-sizing: border-box; margin: 0; padding: 0; }
  html, body {
    width: 1200px; height: 881px; overflow: hidden;
    background: var(--backdrop);
  }
  .sheet {
    position: relative; width: 1200px; height: 881px;
  }
  .card {
    position: absolute; left: 260px; width: 680px; height: 388px;
    border-radius: 22px; overflow: hidden;
    background: linear-gradient(135deg, var(--card-dark) 0%, var(--card-dark-edge) 100%);
    font-family: "Roboto", Arial, sans-serif; color: var(--text-light);
  }
  .card--front { top: 40px; }
  .card--back { top: 453px; }

  /* Front */
  .brand {
    position: absolute; left: 110px; top: 96px;
    display: flex; align-items: center; gap: 18px;
  }
  .brand__square {
    width: 62px; height: 62px; border-radius: 8px;
    background: var(--brand-blue);
  }
  .brand__name {
    font-family: "Montserrat", Arial, sans-serif; font-weight: 700;
    font-size: 46px; letter-spacing: 2px; color: var(--brand-blue);
    text-transform: uppercase; line-height: 1;
  }
  .services {
    position: absolute; left: 0; right: 0; top: 218px; text-align: center;
  }
  .services__title {
    font-family: "Montserrat", Arial, sans-serif; font-weight: 500;
    font-size: 22px; letter-spacing: 1px; color: var(--brand-blue);
    margin-bottom: 12px;
  }
  .services__line {
    font-size: 17px; line-height: 1.6; color: var(--text-light);
  }
  .services__sep { color: var(--brand-blue); padding: 0 4px; }

  /* Back */
  .holder {
    position: absolute; left: 42px; top: 52px;
  }
  .holder__name {
    font-family: "Montserrat", Arial, sans-serif; font-weight: 500;
    font-size: 30px; letter-spacing: 2px; color: var(--brand-blue);
    text-transform: uppercase;
  }
  .holder__role { font-size: 17px; margin-top: 6px; }
  .contacts {
    position: absolute; left: 42px; bottom: 40px; list-style: none;
  }
  .contacts__item {
    display: flex; align-items: center; gap: 10px;
    font-size: 19px; line-height: 1.55;
  }
  .contacts__icon { width: 16px; height: 16px; flex: none; }
  .panel {
    position: absolute; right: 0; top: 0; width: 330px; height: 388px;
  }
  .panel__brand {
    position: absolute; right: 34px; top: 150px;
    display: flex; align-items: center; gap: 12px;
  }
  .panel__square {
    width: 40px; height: 40px; border-radius: 6px; background: var(--brand-blue);
  }
  .panel__name {
    font-family: "Montserrat", Arial, sans-serif; font-weight: 700;
    font-size: 26px; letter-spacing: 1px; color: var(--brand-blue);
    text-transform: uppercase; line-height: 1.1;
  }
</style>
</head>
<body>
<main class="sheet">

  <section class="card card--front" aria-label="Card front">
    <div class="brand">
      <span class="brand__square"></span>
      <span class="brand__name">Fenwar Painting</span>
    </div>
    <div class="services">
      <h2 class="services__title">SERVICES</h2>
      <p class="services__line">Custom Paint &amp; Stain <span class="services__sep">|</span> Interior &amp; Exterior <span class="services__sep">|</span> Epoxy Coatings / Garage Floors</p>
      <p class="services__line">Cabinet Refinishing <span class="services__sep">|</span> Log Staining and Refinishing.</p>
    </div>
  </section>

  <section class="card card--back" aria-label="Card back">
    <svg class="panel" viewBox="0 0 330 388" aria-hidden="true">
      <path d="M110 0 H330 V388 H0 Z" fill="var(--panel-white)"/>
    </svg>
    <div class="panel__brand">
      <span class="panel__square"></span>
      <span class="panel__name">Fenwar<br>Painting</span>
    </div>

    <div class="holder">
      <h1 class="holder__name">Rodrigo Fenwar</h1>
      <p class="holder__role">Director</p>
    </div>

    <ul class="contacts">
      <li class="contacts__item">
        <svg class="contacts__icon" viewBox="0 0 16 16" aria-hidden="true"><path d="M4 1 L6 5 L4.5 6.5 Q6 10 9.5 11.5 L11 10 L15 12 L13.5 15 Q4 14 1 2.5 Z" fill="var(--brand-blue)"/></svg>
        801-437-2190
      </li>
      <li class="contacts__item">
        <svg class="contacts__icon" viewBox="0 0 16 16" aria-hidden="true"><rect x="1" y="3" width="14" height="10" rx="1" fill="none" stroke="var(--brand-blue)" stroke-width="1.5"/><path d="M1.5 3.5 L8 9 L14.5 3.5" fill="none" stroke="var(--brand-blue)" stroke-width="1.5"/></svg>
        Fenwarcoatings.utah@brelmox.com
      </li>
      <li class="contacts__item">
        <svg class="contacts__icon" viewBox="0 0 16 16" aria-hidden="true"><g fill="none" stroke="var(--brand-blue)" stroke-width="1.3"><circle cx="8" cy="8" r="6.5"/><ellipse cx="8" cy="8" rx="3" ry="6.5"/><path d="M1.5 8 H14.5"/></g></svg>
        www.fenwarpainting.utah.com
      </li>
    </ul>
  </section>

</main>
</body>
</html>
```